design a construction company business card

Design business card around our logo. Card must have all the typical info: name, title, address, phone, email, business name, etc. Somewhere on the card I would like to see our motto "Grounded in trust... Driven by dedication." Consider adding a splash of bright orange to the card to complement the blues and silvers/grays in the logo. We are open to metallic inks, textures, etc. We would like to see options on both light and dark backgrounds. The font in the logo is Euro Technic Extended Regular.

```html
<!DOCTYPE html>
<html lang="en">
<head>
<meta charset="utf-8">
<title>Halden Builders – Business Card</title>
<link rel="stylesheet" href="https://fonts.googleapis.com/css2?family=Roboto:ital,wght@0,400;0,700;1,400&display=swap">
<style>
  :root {
    --backdrop: #e4e4e4;
    --paper: #ffffff;
    --orange: #f05a22;
    --orange-light: #f7941d;
    --gray: #808285;
    --ink: #4d4d4f;
    --rule: #d6d6d6;
  }
  * { box-sizing: border-box; margin: 0; padding: 0; }
  html, body {
    width: 1125px; height: 1200px; overflow: hidden;
    background: var(--backdrop);
    font-family: "Roboto", Arial, sans-serif;
  }
  .canvas { position: relative; width: 1125px; height: 1200px; }
  .card {
    position: absolute; left: 171px; width: 826px; height: 472px;
    overflow: hidden;
  }
  .card--front { top: 106px; background: var(--paper); }
  .card--back {
    top: 639px;
    background: linear-gradient(to bottom, var(--orange-light) 0%, var(--orange) 100%);
  }

  /* Front */
  .brand {
    position: absolute; left: 40px; top: 212px; width: 380px;
    display: flex; align-items: center; justify-content: center; gap: 10px;
    color: var(--orange); font-weight: 700; white-space: nowrap;
  }
  .brand__mark { width: 20px; height: 20px; background: var(--orange); flex: none; }
  .brand__name { font-size: 25px; letter-spacing: 0.5px; line-height: 1.15; }
  .divider {
    position: absolute; left: 440px; top: 116px; width: 1px; height: 248px;
    background: var(--rule);
  }
  .details { position: absolute; left: 482px; top: 122px; color: var(--ink); }
  .details__name {
    font-size: 27px; font-weight: 700; color: var(--orange); letter-spacing: 0.5px;
  }
  .details__title { font-size: 18px; color: var(--gray); margin-top: 4px; letter-spacing: 0.5px; }
  .details__address { font-size: 18px; line-height: 25px; margin-top: 17px; letter-spacing: 0.3px; }
  .contact { list-style: none; margin-top: 12px; font-size: 18px; letter-spacing: 0.3px; }
  .contact li { display: flex; align-items: center; gap: 9px; height: 26px; }
  .contact li:first-child { font-size: 19px; }
  .contact svg { width: 17px; height: 17px; flex: none; }
  .stripe { position: absolute; left: 0; bottom: 0; height: 16px; width: 100%; }

  /* Back */
  .back-name {
    position: absolute; left: 0; right: 0; top: 240px; text-align: center;
    color: #fff; font-weight: 700; font-size: 56px; letter-spacing: 3px;
  }
  .motto {
    position: absolute; left: 0; right: 0; top: 344px; text-align: center;
    color: #fff; font-style: italic; font-size: 20px; letter-spacing: 0.2px;
  }
</style>
</head>
<body>
<main class="canvas">
  <section class="card card--front" aria-label="Card front">
    <div class="brand">
      <span class="brand__mark"></span>
      <span class="brand__name">HALDEN BUILDERS, INC.</span>
    </div>
    <div class="divider"></div>
    <div class="details">
      <p class="details__name">MARK ELLISON</p>
      <p class="details__title">CEO/FOUNDER</p>
      <p class="details__address">2140 Birchwood Road<br>Fairbanks, Alaska 99701</p>
      <ul class="contact">
        <li>
          <svg viewBox="0 0 24 24" aria-hidden="true"><path fill="#f05a22" d="M6.6 10.8a15.2 15.2 0 0 0 6.6 6.6l2.2-2.2a1 1 0 0 1 1-.25 11.4 11.4 0 0 0 3.6.57 1 1 0 0 1 1 1V20a1 1 0 0 1-1 1A17 17 0 0 1 3 4a1 1 0 0 1 1-1h3.5a1 1 0 0 1 1 1c0 1.25.2 2.45.57 3.57a1 1 0 0 1-.25 1z"/></svg>
          555 214 7730
        </li>
        <li>
          <svg viewBox="0 0 24 24" aria-hidden="true"><rect x="2" y="5" width="20" height="14" fill="#f05a22"/><path d="M2.5 5.5 12 13l9.5-7.5" fill="none" stroke="#fff" stroke-width="1.6"/></svg>
          mark@haldenbuild.com
        </li>
        <li>
          <svg viewBox="0 0 24 24" aria-hidden="true"><circle cx="12" cy="12" r="10" fill="#f05a22"/><path d="M7 8c2 0 3 1 3 3s-2 2-2 4m7-9c-1 2 0 3 2 3m-3 4c1 1 1 3 0 5" fill="none" stroke="#fff" stroke-width="1.6"/></svg>
          www.haldenbuild.com
        </li>
      </ul>
    </div>
    <svg class="stripe" viewBox="0 0 826 16" preserveAspectRatio="none" aria-hidden="true">
      <defs>
        <linearGradient id="stripeGrad" x1="0" x2="1">
          <stop offset="0" stop-color="#f05a22"/>
          <stop offset="0.5" stop-color="#f7941d"/>
          <stop offset="1" stop-color="#f05a22"/>
        </linearGradient>
      </defs>
      <polygon points="0,0 536,0 531,16 0,16" fill="url(#stripeGrad)"/>
      <polygon points="544,0 826,0 826,16 539,16" fill="#808285"/>
    </svg>
  </section>

  <section class="card card--back" aria-label="Card back">
    <p class="back-name">HALDEN BUILDERS</p>
    <p class="motto">Grounded in trust... Driven by dedication.</p>
  </section>
</main>
</body>
</html>
```